Northvale Strategy Partners Website Design

I need a website design for my new business consulting and executive coaching firm, Northvale Strategy Partners. We provide consultative services to business C-suites as well as personal coaching to executives. I have attached the logo with color scheme I have chosen. I would like the website to reflect professionalism and continue the color scheme in the logo.

Target Market(s)

Small to medium business and their executives; middle to upper income men and women in mid- to late career looking for significance

Industry/Entity Type

Business Consultant

Number of Pages Required

4 page

Requirements
Must have
• A homepage with prominent logo and way to contact for more information; an area on the homepage with easy to read, clear text to describe what the company does; a prominent area on the homepage for a tagline; a blog page that can be updated regularly, an "about us" page with biographical information; an "about us" page; a page detailing services offered
• The web design must match the logo colors and font that I have uploaded.
Nice to have
• A lighthouse picture in the background or header
Should not have
• A lot of text area on the homepage

```html
<!DOCTYPE html>
<html lang="en">
<head>
<meta charset="utf-8">
<title>Northvale Strategy Partners</title>
<link href="https://fonts.googleapis.com/css2?family=Cinzel:wght@400;600&family=Open+Sans:wght@400;600;700&display=swap" rel="stylesheet">
<style>
  :root {
    --navy: #1f3d8c;
    --navy-deep: #162c66;
    --red: #a51f2b;
    --red-deep: #7e1620;
    --ink: #333333;
    --muted: #7a7a7a;
    --rule: #cfcfd4;
    --grey-band: #e8e8eb;
    --footer: #2a2a2c;
    --white: #ffffff;
  }
  * { box-sizing: border-box; margin: 0; padding: 0; }
  html, body { width: 1200px; height: 2520px; overflow: hidden; }
  body { font-family: "Open Sans", Arial, sans-serif; color: var(--ink); background: var(--white); }
  .page { position: relative; width: 1200px; height: 2520px; overflow: hidden; }
  section, header, footer { position: absolute; left: 0; width: 1200px; }

  /* Hero */
  .hero { top: 0; height: 596px; }
  .hero-photo { position: absolute; inset: 0; width: 1200px; height: 596px; }
  .main-nav { position: absolute; top: 0; left: 0; width: 1200px; height: 62px; background: rgba(20,20,22,0.45);
    display: flex; justify-content: center; gap: 0; }
  .main-nav a { display: block; padding: 22px 24px 0; height: 62px; font-size: 12px; font-weight: 600; letter-spacing: 1px;
    color: var(--white); text-decoration: none; text-transform: uppercase; }
  .main-nav a.is-active { background: var(--red); border-bottom: 3px solid #e2e2e2; }
  .brand { position: absolute; top: 190px; left: 0; width: 1200px; text-align: center; color: var(--white); }
  .brand-mark { display: inline-block; width: 22px; height: 22px; background: var(--white); margin-bottom: 18px; }
  .brand-name { font-family: "Cinzel", Georgia, serif; font-weight: 600; font-size: 44px; line-height: 52px; letter-spacing: 3px; }
  .tagline { position: absolute; top: 338px; width: 1200px; text-align: center; color: var(--white);
    font-size: 26px; font-weight: 600; line-height: 36px; text-shadow: 0 2px 6px rgba(0,0,0,0.35); }
  .slider-dots { position: absolute; top: 542px; width: 1200px; display: flex; justify-content: center; gap: 10px; }
  .slider-dots span { width: 10px; height: 10px; border-radius: 50%; background: rgba(255,255,255,0.55); }
  .slider-dots span.on { background: var(--white); }

  /* Shared */
  .divider { position: absolute; left: 80px; width: 1040px; height: 24px; }
  .divider::before, .divider::after { content: ""; position: absolute; top: 11px; width: 490px; height: 1px; background: var(--rule); }
  .divider::before { left: 0; }
  .divider::after { right: 0; }
  .divider i { position: absolute; left: 508px; top: 0; width: 24px; height: 24px; background: var(--navy); border-bottom: 5px solid var(--red); }
  .section-title { font-family: "Cinzel", Georgia, serif; font-weight: 400; color: var(--navy); }
  .section-title em { font-style: normal; color: var(--red); }
  .body-copy { font-size: 14px; line-height: 23px; color: var(--muted); }
  .btn-outline { display: inline-block; width: 160px; height: 48px; line-height: 46px; text-align: center;
    border: 1px solid #9a9a9a; font-family: "Cinzel", Georgia, serif; font-size: 15px; color: var(--ink); }

  /* Welcome */
  .welcome { top: 596px; height: 284px; }
  .welcome .divider { top: 40px; }
  .welcome .section-title { position: absolute; top: 92px; width: 1200px; text-align: center; font-size: 40px; }
  .welcome .body-copy { position: absolute; top: 160px; left: 110px; width: 980px; text-align: center; }

  /* Services */
  .service { height: 460px; }
  .service-photo { position: absolute; top: 0; left: 0; }
  .service-label { font-family: "Cinzel", Georgia, serif; font-size: 16px; color: var(--ink); }
  .service-title { font-family: "Cinzel", Georgia, serif; font-size: 36px; line-height: 44px; }
  .service-text { position: absolute; width: 470px; }
  .service-text .body-copy { margin: 18px 0 26px; }
  .consulting { top: 880px; }
  .consulting .service-text { left: 72px; top: 140px; }
  .consulting .service-title { color: var(--navy); }
  .coaching { top: 1330px; height: 410px; }
  .coaching .service-text { right: 70px; top: 108px; text-align: right; }
  .coaching .service-title { color: var(--red); }

  /* Blog */
  .blog { top: 1740px; height: 380px; background: var(--grey-band); }
  .blog .section-title { position: absolute; top: 118px; width: 1200px; text-align: center; font-size: 38px; }
  .blog .title-rule { position: absolute; top: 176px; left: 360px; width: 480px; height: 1px; background: #c4c4ca; }
  .blog .body-copy { position: absolute; top: 196px; left: 170px; width: 860px; text-align: center; }
  .post-date { position: absolute; top: 252px; width: 1200px; text-align: center; font-size: 14px; font-weight: 700; color: var(--red); }
  .blog-dots { position: absolute; top: 308px; width: 1200px; display: flex; justify-content: center; gap: 8px; }
  .blog-dots span { width: 9px; height: 9px; border-radius: 50%; background: #b9bcc8; }
  .blog-dots span.on { background: var(--navy); }

  /* Clients */
  .clients { top: 2120px; height: 240px; }
  .clients .divider { top: 32px; }
  .clients .section-title { position: absolute; top: 82px; width: 1200px; text-align: center; font-size: 36px; }
  .client-list { position: absolute; top: 166px; left: 150px; width: 900px; display: flex; justify-content: space-between;
    list-style: none; font-size: 15px; font-weight: 600; color: #6b6b6b; }

  /* Footer */
  .site-footer { top: 2360px; height: 160px; background: var(--footer); }
  .copyright { position: absolute; top: 52px; width: 1200px; text-align: center; font-size: 12px; color: #8d8d90; }
  .social { position: absolute; top: 86px; width: 1200px; display: flex; justify-content: center; gap: 18px; list-style: none; }
  .social li { width: 16px; height: 16px; border-radius: 50%; background: #9a9a9e; }
</style>
</head>
<body>
<div class="page">

  <header class="hero">
    <svg class="hero-photo" viewBox="0 0 1200 596" role="img" aria-label="Photograph of a lighthouse on a rocky coast under a hazy sky with a flock of birds">
      <defs>
        <linearGradient id="heroSky" x1="0" y1="0" x2="0" y2="1">
          <stop offset="0" stop-color="#6d6458"/>
          <stop offset="0.45" stop-color="#a39a89"/>
          <stop offset="0.75" stop-color="#7c7462"/>
          <stop offset="1" stop-color="#3f3a31"/>
        </linearGradient>
        <radialGradient id="heroGlow" cx="0.55" cy="0.4" r="0.5">
          <stop offset="0" stop-color="#d6ccb6" stop-opacity="0.55"/>
          <stop offset="1" stop-color="#d6ccb6" stop-opacity="0"/>
        </radialGradient>
      </defs>
      <rect width="1200" height="596" fill="url(#heroSky)"/>
      <rect width="1200" height="596" fill="url(#heroGlow)"/>
    </svg>

    <nav class="main-nav">
      <a class="is-active">Home</a>
      <a>About</a>
      <a>Services</a>
      <a>Latest News</a>
      <a>Blog</a>
      <a>Clients</a>
      <a>Coaching</a>
      <a>Contact Us</a>
    </nav>

    <div class="brand">
      <span class="brand-mark"></span>
      <div class="brand-name">Northvale<br>Strategy Partners</div>
    </div>

    <p class="tagline">We provide consultative services to business C-suites<br>as well as personal coaching to executives.</p>

    <div class="slider-dots"><span class="on"></span><span></span><span></span></div>
  </header>

  <section class="welcome">
    <div class="divider"><i></i></div>
    <h1 class="section-title">Welcome to <em>Northvale Strategy Partners</em></h1>
    <p class="body-copy">Northvale Strategy Partners works beside owners and senior leaders of growing companies to sharpen direction, align teams and turn plans into steady results. We listen first, study how your business truly runs, then shape practical steps your people can carry forward. Our coaches also meet executives one to one, helping them lead with clarity, confidence and purpose through every stage of a demanding career.</p>
  </section>

  <section class="service consulting">
    <svg class="service-photo" width="1200" height="460" viewBox="0 0 1200 460" role="img" aria-label="Blue-toned photograph of business people meeting around a table">
      <defs>
        <linearGradient id="consultTone" x1="0" y1="0" x2="1" y2="1">
          <stop offset="0" stop-color="#2a4ea6"/>
          <stop offset="1" stop-color="#13285e"/>
        </linearGradient>
      </defs>
      <polygon points="0,0 1200,0 1200,450" fill="url(#consultTone)"/>
      <polygon points="0,0 120,0 0,45" fill="var(--navy-deep)"/>
    </svg>
    <div class="service-text">
      <p class="service-label">Our Services</p>
      <h2 class="service-title">Business Consulting</h2>
      <p class="body-copy">We help C-suite teams review strategy, structure and growth plans with a fresh outside view. Together we set clear priorities, measure what matters and build the habits that keep a company moving toward its goals year after year.</p>
      <span class="btn-outline">Read More</span>
    </div>
  </section>

  <section class="service coaching">
    <svg class="service-photo" width="1200" height="410" viewBox="0 0 1200 410" role="img" aria-label="Red-toned photograph of an executive coaching session">
      <defs>
        <linearGradient id="coachTone" x1="0" y1="0" x2="1" y2="1">
          <stop offset="0" stop-color="#b8262f"/>
          <stop offset="1" stop-color="#6f121b"/>
        </linearGradient>
      </defs>
      <polygon points="0,0 1100,0 0,400" fill="url(#coachTone)"/>
    </svg>
    <div class="service-text">
      <p class="service-label">Our Services</p>
      <h2 class="service-title">Executive Coaching</h2>
      <p class="body-copy">Private coaching for leaders in mid to late career who want more than success. We explore strengths, values and next steps, so each executive can lead well, live fully and leave a lasting mark on the people around them.</p>
      <span class="btn-outline">Read More</span>
    </div>
  </section>

  <section class="blog">
    <h2 class="section-title">Latest Blog Posts</h2>
    <div class="title-rule"></div>
    <p class="body-copy">How small leadership teams can plan for the year ahead: three questions every founder should ask before setting new targets, and why honest answers matter more than bold forecasts when the goal is growth that lasts.</p>
    <p class="post-date">Posted on Dec 30, 2015</p>
    <div class="blog-dots"><span class="on"></span><span></span><span></span></div>
  </section>

  <section class="clients">
    <div class="divider"><i></i></div>
    <h2 class="section-title">Our Clients</h2>
    <ul class="client-list">
      <li>Pembury Grocers</li>
      <li>Searchly</li>
      <li>Linkwork</li>
      <li>Ledgerly</li>
      <li>Korvex</li>
      <li>Telbridge</li>
      <li>Quadrasoft</li>
      <li>Arcform</li>
      <li>Netspire</li>
    </ul>
  </section>

  <footer class="site-footer">
    <p class="copyright">Copyright © 2015 Northvale Strategy Partners. All Rights Reserved.</p>
    <ul class="social"><li></li><li></li><li></li><li></li><li></li></ul>
  </footer>

</div>
</body>
</html>
```